VOX Mission & Values Poster design

The company has developed a new Mission/Purpose statement and new core values which we want to communicate broadly. We are looking for an engaging poster design which illustrates the importance of the values.

An extract of the presentation to announce the update to mission and values as well as an extract of the new hire orientation are attached for reference regarding the company. Also attaching the company logo file for your use/reference.

Target Market(s)

Employees

Industry/Entity Type

Energy

Requirements
Must have
• Logo and brand consistency, engaging messaging and imagery
Should not have
• Wind or Oil industry imagery or references

```html
<!DOCTYPE html>
<html lang="en">
<head>
<meta charset="utf-8">
<title>VOX Values Poster</title>
<link href="https://fonts.googleapis.com/css2?family=Poppins:wght@400;600;700;800&display=swap" rel="stylesheet">
<style>
  :root {
    --crimson: #c8123f;
    --crimson-deep: #9c0d33;
    --leaf: #6aa83a;
    --leaf-pale: #dfeccf;
    --olive: #9a9a3c;
    --ink: #111111;
    --paper: #ffffff;
    --night: #000000;
  }
  * { margin: 0; padding: 0; box-sizing: border-box; }
  html, body { width: 970px; height: 1200px; overflow: hidden; background: var(--paper); }
  body { font-family: "Poppins", sans-serif; color: var(--ink); }
  .poster { position: relative; width: 970px; height: 1200px; overflow: hidden; background: var(--paper); }

  .hero-ring { position: absolute; left: 0; top: 0; }
  .hero-title {
    position: absolute; left: 80px; top: 312px;
    font-weight: 700; font-size: 52px; line-height: 56px; color: var(--paper);
    letter-spacing: 0.5px;
  }

  .value { position: absolute; }
  .value-badge { position: absolute; }
  .value-name { font-weight: 700; font-size: 27px; line-height: 30px; letter-spacing: 0.3px; }
  .value-name.is-crimson { color: var(--crimson); }
  .value-name.is-leaf { color: var(--leaf); }
  .value-text { font-size: 13.4px; line-height: 16.6px; margin-top: 2px; }

  .skyline { position: absolute; left: 0; top: 760px; width: 970px; height: 120px;
    background: linear-gradient(to bottom, rgba(0,0,0,0) 0%, rgba(0,0,0,0.55) 45%, var(--night) 100%); }
  .footer-band { position: absolute; left: 0; top: 878px; width: 970px; height: 322px; background: var(--night); }

  .brand { position: absolute; left: 70px; top: 1010px; display: flex; align-items: center; gap: 14px; }
  .brand-dot { width: 40px; height: 40px; border-radius: 50%; background: var(--crimson); }
  .brand-name { font-weight: 700; font-size: 28px; color: var(--olive); }

  .mission { position: absolute; left: 452px; top: 940px; width: 450px; }
  .mission-title { font-weight: 800; font-size: 37px; line-height: 40px; color: var(--crimson); }
  .mission-sub { font-weight: 800; font-size: 31px; line-height: 36px; color: var(--leaf); }
  .mission-text { margin-top: 14px; font-weight: 600; font-size: 16.8px; line-height: 20px; color: var(--paper); }
</style>
</head>
<body>
<main class="poster">

  <svg class="hero-ring" width="420" height="660" viewBox="0 0 420 660">
    <defs>
      <linearGradient id="ringFade" x1="0" y1="0" x2="0" y2="1">
        <stop offset="0" stop-color="#eef5e6"/>
        <stop offset="1" stop-color="#6aa83a"/>
      </linearGradient>
      <radialGradient id="heroFill" cx="0.4" cy="0.4" r="0.7">
        <stop offset="0" stop-color="#b8123f"/>
        <stop offset="1" stop-color="#930c30"/>
      </radialGradient>
    </defs>
    <path d="M 80 102 A 272 272 0 0 1 80 632" fill="none" stroke="url(#ringFade)" stroke-width="3.5" transform="translate(0,0)"/>
    <circle cx="135" cy="366" r="230" fill="url(#heroFill)" role="img" aria-label="Team of employees standing together in front of the plant, tinted crimson"/>
  </svg>
  <h1 class="hero-title">VOX’S<br>VALUES</h1>

  <!-- Safety -->
  <svg class="value-badge" style="left:290px;top:46px" width="66" height="64" viewBox="0 0 66 64" role="img" aria-label="Safety icon: worker with hard hat">
    <path d="M4 58 L12 44 L20 52 Z" fill="var(--crimson)"/><circle cx="34" cy="31" r="30" fill="var(--crimson)"/>
  </svg>
  <section class="value" style="left:375px;top:42px;width:500px">
    <h2 class="value-name is-crimson">SAFETY</h2>
    <p class="value-text">Safety is VOX's top priority for our employees, our customers, and the community. Providing a safe and healthy work environment is an individual and shared responsibility. We never sacrifice safety to achieve results. Our goal is an injury free workplace.</p>
  </section>

  <!-- People -->
  <svg class="value-badge" style="left:400px;top:168px" width="70" height="64" viewBox="0 0 70 64" role="img" aria-label="People icon: hands holding a group">
    <path d="M2 40 L14 30 L16 46 Z" fill="var(--leaf)"/><circle cx="38" cy="32" r="30" fill="var(--leaf)"/>
  </svg>
  <section class="value" style="left:487px;top:182px;width:360px">
    <h2 class="value-name is-leaf">PEOPLE</h2>
    <p class="value-text">Our employees are the key to our success. We foster a culture of diversity, inclusion, trust, respect, accountability, and engagement where our employees can grow both professionally and personally within our community. We invest in our people to allow them to grow professionally and personally.</p>
  </section>

  <!-- Environment -->
  <svg class="value-badge" style="left:428px;top:345px" width="70" height="64" viewBox="0 0 70 64" role="img" aria-label="Environment icon: hand holding a globe with a sprout">
    <path d="M2 30 L16 22 L16 40 Z" fill="var(--crimson)"/><circle cx="38" cy="31" r="30" fill="var(--crimson)"/>
  </svg>
  <section class="value" style="left:518px;top:358px;width:350px">
    <h2 class="value-name is-crimson">ENVIRONMENT</h2>
    <p class="value-text">Environmental stewardship is embedded in our culture through energy efficiency and resource conservation to comply, adapt, and drive our business sustainably for today and generations to come</p>
  </section>

  <!-- Growth -->
  <svg class="value-badge" style="left:393px;top:487px" width="68" height="64" viewBox="0 0 68 64">
    <path d="M2 4 L18 10 L10 20 Z" fill="var(--leaf)"/><circle cx="36" cy="32" r="30" fill="var(--leaf)"/>
    <g fill="none" stroke="#fff" stroke-width="1.6">
      <rect x="24" y="38" width="5" height="7"/><rect x="31" y="34" width="5" height="11"/><rect x="38" y="30" width="5" height="15"/><rect x="45" y="25" width="5" height="20"/>
      <path d="M22 32 L32 26 L38 28 L49 18"/><path d="M44 18 L49 18 L49 23"/>
    </g>
  </svg>
  <section class="value" style="left:484px;top:500px;width:392px">
    <h2 class="value-name is-leaf">GROWTH</h2>
    <p class="value-text">We embrace innovation to drive new ideas, creativity, and collaboration to empower continuous improvement in our processes and system efficiencies to grow our business. We drive continuous expansion and growth of our customer base at NGP. We help improve our community through charitable activity.</p>
  </section>

  <!-- Reliability -->
  <svg class="value-badge" style="left:290px;top:650px" width="66" height="64" viewBox="0 0 66 64" role="img" aria-label="Reliability icon: handshake with service symbols">
    <path d="M4 4 L20 10 L12 20 Z" fill="var(--crimson)"/><circle cx="34" cy="32" r="30" fill="var(--crimson)"/>
  </svg>
  <section class="value" style="left:377px;top:663px;width:470px">
    <h2 class="value-name is-crimson">RELIABILITY</h2>
    <p class="value-text">We are dedicated to providing efficient and resilient utility services with industry leading reliability, enabling our customers to achieve their business goals.</p>
  </section>

  <div class="skyline" role="img" aria-label="Silhouette of an industrial plant skyline with stacks and piping"></div>
  <div class="footer-band"></div>

  <div class="brand">
    <span class="brand-dot"></span>
    <span class="brand-name">VOX Energy, LLC</span>
  </div>

  <section class="mission">
    <h2 class="mission-title">MISSION &amp; VISION</h2>
    <h3 class="mission-sub">PURPOSE STATEMENT</h3>
    <p class="mission-text">Through our unwavering commitment to safety, reliability, environmental stewardship, and community, we strive to be a trusted utilities provider that drives sustainable development, powers progress, and leads the way towards a greener and brighter future.</p>
  </section>

</main>
</body>
</html>
```